Design for a 4 screens iOS and Android app - "VelaTrakko"

The app allows you to track your car gasoline refill ...
We need a design for the 4 screens of the app:
a) 1 form with 3 fields.
b) 1 simple list view
c) 1 summary view
d) 1 text page
2 "alerts" items are also to be designed.
No specific guidelines, nor logo or whatever.
It will be a free app distributed on iOS and Androïd.
We just want to make it looking nice & very usable for end users.
Target Market(s)
B2C app
Industry/Entity Type
Android

```html
<!DOCTYPE html>
<html lang="en">
<head>
<meta charset="utf-8">
<title>VelaTrakko – Monthly summary</title>
<link href="https://fonts.googleapis.com/css2?family=Roboto:wght@400;900&display=swap" rel="stylesheet">
<style>
  :root {
    --brand-blue: #0a8bfb;
    --text-blue: #1a8af0;
    --panel-bg: #d9effc;
    --page-bg: #ffffff;
    --white: #ffffff;
  }
  * { box-sizing: border-box; margin: 0; padding: 0; }
  html, body {
    width: 675px;
    height: 1200px;
    overflow: hidden;
    background: var(--page-bg);
    font-family: "Roboto", sans-serif;
  }
  .app-screen {
    width: 675px;
    height: 1200px;
    overflow: hidden;
    position: relative;
  }
  .tab-bar {
    display: flex;
    height: 106px;
    background: var(--brand-blue);
  }
  .tab-item {
    flex: 1;
    display: flex;
    align-items: center;
    justify-content: center;
  }
  .tab-item + .tab-item { border-left: 1px solid var(--white); }
  .tab-item svg { display: block; }

  .month-header {
    height: 108px;
    display: flex;
    align-items: center;
    justify-content: center;
    font-weight: 900;
    font-size: 30px;
    color: var(--brand-blue);
    letter-spacing: 0.3px;
    word-spacing: 8px;
  }
  .month-summary {
    height: 324px;
    background: var(--panel-bg);
    padding: 52px 41px 0 35px;
  }
  .stat-row {
    display: flex;
    justify-content: space-between;
    align-items: center;
    height: 56px;
    font-size: 30px;
    font-weight: 400;
    color: var(--text-blue);
  }
</style>
</head>
<body>
<main class="app-screen">
  <nav class="tab-bar">
    <div class="tab-item" aria-label="Add refill">
      <svg width="46" height="46" viewBox="0 0 46 46" fill="none" stroke="#fff" stroke-width="4" stroke-linecap="round">
        <line x1="23" y1="2" x2="23" y2="44"/><line x1="2" y1="23" x2="44" y2="23"/>
      </svg>
    </div>
    <div class="tab-item" aria-label="Refill list">
      <svg width="62" height="44" viewBox="0 0 62 44" fill="#fff" stroke="#fff" stroke-width="3.5" stroke-linecap="round">
        <circle cx="5" cy="4" r="4" stroke="none"/><circle cx="5" cy="22" r="4" stroke="none"/><circle cx="5" cy="40" r="4" stroke="none"/>
        <line x1="18" y1="4" x2="60" y2="4"/><line x1="18" y1="22" x2="60" y2="22"/><line x1="18" y1="40" x2="60" y2="40"/>
      </svg>
    </div>
    <div class="tab-item" aria-label="Statistics">
      <svg width="58" height="46" viewBox="0 0 58 46" fill="#fff">
        <path d="M2 2 V44 H57" fill="none" stroke="#fff" stroke-width="3.5" stroke-linecap="round"/>
        <path d="M9 38 V20 L16 12 L26 22 L36 12 L50 30 L52 38 Z"/>
      </svg>
    </div>
  </nav>

  <section>
    <h2 class="month-header">February 2016</h2>
    <div class="month-summary">
      <div class="stat-row"><span>Total cost</span><span>570€</span></div>
      <div class="stat-row"><span>Mileage</span><span>7500 km</span></div>
      <div class="stat-row"><span>Full tanks</span><span>11</span></div>
      <div class="stat-row"><span>Consumption</span><span>6,5 l</span></div>
    </div>
  </section>

  <section>
    <h2 class="month-header">January 2016</h2>
    <div class="month-summary">
      <div class="stat-row"><span>Total cost</span><span>241€</span></div>
      <div class="stat-row"><span>Mileage</span><span>2770 km</span></div>
      <div class="stat-row"><span>Full tanks</span><span>4</span></div>
      <div class="stat-row"><span>Consumption</span><span>6,2 l</span></div>
    </div>
  </section>

  <section>
    <h2 class="month-header">December 2015</h2>
    <div class="month-summary">
      <div class="stat-row"><span>Total cost</span><span>180€</span></div>
      <div class="stat-row"><span>Mileage</span><span></span></div>
    </div>
  </section>
</main>
</body>
</html>
```